TA BRAMLEY BUSINESS CARD DESIGN PROJECT

We need to utilize our logo that was expertly created on PixelHarbor and now need to match this with a business card design.

```html
<!DOCTYPE html>
<html lang="en">
<head>
<meta charset="utf-8">
<title>TA BRAMLEY Business Card</title>
<link href="https://fonts.googleapis.com/css2?family=Montserrat:wght@400;700;800&display=swap" rel="stylesheet">
<style>
  :root {
    --page: #d9d9d6;
    --white: #ffffff;
    --ink: #181818;
    --blue: #0f57a8;
    --text-light: #f2f2f2;
  }
  * { box-sizing: border-box; margin: 0; padding: 0; }
  html, body { width: 1200px; height: 801px; overflow: hidden; }
  body {
    background: var(--page);
    font-family: "Montserrat", Arial, sans-serif;
    position: relative;
  }
  .card {
    position: absolute;
    top: 246px;
    width: 540px;
    height: 309px;
    overflow: hidden;
    box-shadow: 0 10px 24px rgba(0,0,0,0.18);
  }
  .card-front { left: 40px; background: var(--white); }
  .card-back { left: 620px; background: var(--blue); }

  .front-shape { position: absolute; inset: 0; width: 100%; height: 100%; }

  .front-brand {
    position: absolute;
    left: 24px;
    top: 112px;
    display: flex;
    align-items: center;
    gap: 8px;
    color: var(--blue);
    font-weight: 800;
    font-size: 22px;
    letter-spacing: 1px;
    white-space: nowrap;
  }
  .brand-mark {
    width: 14px; height: 14px;
    background: var(--blue);
    flex: none;
  }

  .contact-accent {
    position: absolute;
    right: 30px;
    top: 0;
    width: 30px;
    height: 20px;
    background: var(--blue);
  }

  .contact {
    position: absolute;
    right: 30px;
    top: 44px;
    width: 220px;
    color: var(--text-light);
    text-align: right;
    font-size: 12px;
    line-height: 1.45;
  }
  .contact-name {
    color: var(--blue);
    font-weight: 700;
    font-size: 17px;
    letter-spacing: 0.5px;
  }
  .contact-title { font-size: 13px; margin-bottom: 12px; }
  .contact-address { margin-bottom: 12px; }
  .contact-line { display: flex; justify-content: flex-end; align-items: center; gap: 6px; }
  .contact-line svg { width: 10px; height: 10px; flex: none; }

  .back-brand {
    position: absolute;
    inset: 0;
    display: flex;
    align-items: center;
    justify-content: center;
    gap: 16px;
    color: var(--white);
    font-weight: 800;
    font-size: 46px;
    letter-spacing: 4px;
  }
  .back-brand .brand-mark { width: 24px; height: 24px; background: var(--white); }
</style>
</head>
<body>
  <section class="card card-front">
    <svg class="front-shape" viewBox="0 0 540 309" preserveAspectRatio="none" aria-hidden="true">
      <path d="M330,0 C250,60 265,200 150,309" fill="none" stroke="#0f57a8" stroke-width="8"/>
      <path d="M344,0 C264,60 282,205 170,309 L540,309 L540,0 Z" fill="#181818"/>
      <path d="M338,0 C258,60 274,202 160,309" fill="none" stroke="#ffffff" stroke-width="3"/>
      <path d="M0,300 C60,300 110,290 150,260" fill="none" stroke="#0f57a8" stroke-width="6"/>
    </svg>

    <div class="front-brand"><span class="brand-mark"></span>TA BRAMLEY</div>

    <span class="contact-accent"></span>
    <div class="contact">
      <p class="contact-name">JORDAN BLAKE</p>
      <p class="contact-title">Managing Director</p>
      <p class="contact-address">Your address, City<br>State, Zip 1234</p>
      <p class="contact-line">123 456 789
        <svg viewBox="0 0 10 10"><path d="M2,1 L4,1 L5,3 L4,4 Q5,6 6,6 L7,5 L9,6 L9,8 Q5,9 1,3 Z" fill="#0f57a8"/></svg></p>
      <p class="contact-line">info@yourmail.com
        <svg viewBox="0 0 10 10"><rect x="0.5" y="2" width="9" height="6" fill="#0f57a8"/><path d="M0.5,2 L5,5.5 L9.5,2" fill="none" stroke="#181818" stroke-width="1"/></svg></p>
      <p class="contact-line">www.yourwebsite.com
        <svg viewBox="0 0 10 10"><circle cx="5" cy="5" r="4.5" fill="#0f57a8"/></svg></p>
    </div>
  </section>

  <section class="card card-back">
    <div class="back-brand"><span class="brand-mark"></span>TA BRAMLEY</div>
  </section>
</body>
</html>
```